Merry Meadow Roasters

We need a website to sell coffee with a horse theme. We already have a logo and have designed 4 different coffee bags/flavors so far, each of which will be available in ground or whole bean. The brand is intended to be light hearted/whimsical.

Requirements
Must have
• incorporation of attached photos
Nice to have
• underlying background theme with sky/grass

```html
<!DOCTYPE html>
<html lang="en">
<head>
<meta charset="utf-8">
<title>Merry Meadow Roasters</title>
<link href="https://fonts.googleapis.com/css2?family=Lobster&family=Open+Sans:wght@400;600;700&display=swap" rel="stylesheet">
<style>
:root{
  --cream:#fdebd9;
  --dark:#2d2a29;
  --orange:#c98536;
  --rust:#9b3e24;
  --plum:#4d4246;
  --ink:#3b2a21;
  --white:#ffffff;
}
*{box-sizing:border-box;margin:0;padding:0}
html,body{width:1200px;height:3834px;overflow:hidden}
body{position:relative;background:var(--cream);font-family:"Open Sans",Arial,sans-serif;color:var(--ink)}
.abs{position:absolute}
.script{font-family:"Lobster",cursive;font-weight:400}
.btn{position:absolute;display:flex;align-items:center;justify-content:center;background:var(--orange);color:var(--white);font-weight:700;font-size:16px;border-radius:4px;text-transform:uppercase}

/* hero */
.hero{left:0;top:0;width:1200px;height:620px;background:linear-gradient(135deg,#3f3c3a 0%,#2e2b2a 45%,#232020 100%);
 clip-path:polygon(0 0,1200px 0,1200px 535px,1120px 540px,1040px 548px,960px 552px,880px 568px,800px 563px,720px 585px,640px 576px,560px 592px,470px 600px,380px 582px,300px 602px,210px 616px,130px 592px,60px 612px,0 596px)}
.hero-bowl{left:760px;top:150px;width:330px;height:380px;border-radius:50%;background:radial-gradient(circle at 50% 50%,#6a3420 0%,#4a2314 55%,#2e1710 80%,rgba(40,25,20,0) 100%)}
.hero-cup{left:780px;top:0;width:210px;height:150px;border-radius:0 0 50% 50%;background:radial-gradient(circle at 50% 30%,#8a4a28,#4a2a1c 70%,rgba(40,30,28,0))}
.hero-bag{left:655px;top:162px;width:138px;height:218px;border-radius:6px;background:linear-gradient(180deg,#d9c7ab 0%,#c6ab86 65%,#4a2f22 100%)}
.brand{display:flex;align-items:center;gap:10px;color:var(--white);font-weight:700}
.brand-dot{width:14px;height:14px;border-radius:50%;background:var(--white);flex:none}
.nav-item{position:absolute;top:53px;font-size:14px;font-weight:700;color:var(--white);text-transform:uppercase;white-space:nowrap}
.nav-item.active{color:var(--orange);font-size:16px;top:51px}
.icon-btn{position:absolute;top:38px;width:46px;height:46px;border-radius:50%;display:flex;align-items:center;justify-content:center}
.hero-dots{left:52px;top:260px;display:flex;flex-direction:column;gap:8px}
.hero-dots span{width:9px;height:9px;border-radius:50%;background:var(--white)}
.hero-dots span:first-child{background:var(--orange)}

/* section marks and titles */
.mark{position:absolute;width:30px;height:30px;border-radius:50%;background:var(--ink)}
.mark.light{background:var(--white)}
.title{position:absolute;left:0;width:1200px;text-align:center;font-family:"Lobster",cursive;font-size:50px;color:var(--ink)}

/* products */
.card{position:absolute;top:849px;width:224px;height:380px}
.card.featured::before{content:"";position:absolute;left:0;top:104px;width:224px;height:216px;background:var(--plum);border-radius:16px 16px 0 0}
.bag{position:absolute;left:28px;top:0;width:168px;height:268px;border-radius:6px;background:linear-gradient(180deg,#dccab0 0%,#cdb491 55%,#b39872 70%,#4a2f22 71%,#3e2719 100%)}
.card-name{position:absolute;left:0;top:277px;width:224px;text-align:center;font-family:"Lobster",cursive;font-size:21px;color:var(--ink)}
.featured .card-name{color:var(--white)}
.card .btn{left:0;top:320px;width:224px;height:60px;font-size:13px;border-radius:2px}
.badge{left:505px;top:834px;width:76px;height:76px;border-radius:50%;background:var(--rust);color:var(--white);text-align:center;font-family:"Lobster",cursive;line-height:1;padding-top:13px;font-size:26px}
.badge small{display:block;font-size:14px}
.arrow{position:absolute;width:38px;height:38px;border-radius:50%;display:flex;align-items:center;justify-content:center}

/* about */
.about{left:0;top:1310px;width:1200px;height:640px;background:
 radial-gradient(ellipse 260px 150px at 720px 430px,#cfc6be 0%,#9a8d84 40%,rgba(90,58,40,0) 75%),
 radial-gradient(ellipse 360px 300px at 1080px 360px,#7a4a2c 0%,#4a2a1a 60%,rgba(60,38,26,0) 100%),
 linear-gradient(90deg,#2c211c 0%,#3b2a22 45%,#4d3324 75%,#3d261a 100%);
 clip-path:polygon(0 40px,80px 30px,160px 42px,240px 22px,330px 30px,420px 10px,520px 25px,600px 8px,700px 20px,800px 12px,880px 28px,960px 15px,1040px 30px,1120px 18px,1200px 10px,1200px 640px,0 640px)}
.about-text{left:103px;top:1586px;width:480px;font-size:15px;line-height:25px;color:var(--white)}

/* testimonials */
.testi{left:0;top:1890px;width:1200px;height:515px;background:var(--rust);
 clip-path:polygon(0 36px,90px 28px,180px 40px,270px 20px,360px 34px,450px 22px,540px 38px,640px 24px,730px 34px,820px 18px,920px 30px,1010px 20px,1100px 34px,1200px 22px,1200px 515px,0 515px)}
.quote{position:absolute;top:2135px;width:450px;height:191px;border:2px solid var(--orange);border-radius:95px 0 95px 95px;display:flex;align-items:center;gap:18px;padding-left:16px;color:var(--white)}
.quote.filled{background:var(--orange)}
.avatar{width:150px;height:150px;border-radius:50%;flex:none;background:radial-gradient(circle at 50% 40%,#d9b79a,#6b3f2c)}
.quote .stars{font-size:22px;letter-spacing:3px}
.quote p{font-size:14px;font-style:italic;line-height:21px;margin:6px 0}
.quote .who{font-family:"Lobster",cursive;font-size:22px}

/* portfolio */
.shot{position:absolute}

/* footer */
.footer{left:0;top:3300px;width:1200px;height:534px;background:linear-gradient(180deg,#8f4d34 0%,#7d4129 100%);
 clip-path:polygon(0 78px,100px 70px,200px 84px,300px 60px,400px 72px,500px 48px,600px 60px,700px 36px,800px 50px,900px 30px,1000px 42px,1100px 24px,1200px 30px,1200px 534px,0 534px)}
.foot-head{position:absolute;font-family:"Lobster",cursive;font-size:22px;color:var(--white)}
.foot-links{left:447px;top:3478px;list-style:none;font-size:15px;color:var(--white);line-height:31px}
.contact-row{position:absolute;left:640px;display:flex;gap:14px;color:var(--white);font-size:14px;line-height:20px}
.contact-row b{font-size:13px}
.c-icon{width:40px;height:40px;border-radius:50%;background:var(--rust);flex:none;display:flex;align-items:center;justify-content:center}
.social{position:absolute;top:3475px;width:46px;height:46px;border-radius:50%;border:2px solid var(--white)}
.social.on{background:var(--white);border-color:var(--rust)}
.divider{left:135px;top:3690px;width:930px;height:1px;background:rgba(255,255,255,.35)}
.copy{left:0;top:3703px;width:1200px;text-align:center;color:var(--white);font-size:14px}
.beans{left:0;top:3730px;width:1200px;height:104px;background:linear-gradient(180deg,rgba(80,40,22,0) 0%,#5a2c18 45%,#3a1c10 100%)}
</style>
</head>
<body>

<!-- HERO -->
<section class="abs hero" aria-label="Welcome">
  <div class="abs hero-cup" role="img" aria-label="Cup of ground coffee"></div>
  <div class="abs hero-bowl" role="img" aria-label="Bowl of roasted coffee beans with green leaves"></div>
  <div class="abs hero-bag" role="img" aria-label="Coffee bag"></div>
</section>
<div class="abs brand" style="left:104px;top:40px;font-size:17px;line-height:20px;width:170px">
  <span class="brand-dot"></span><span>Merry Meadow<br>Roasters</span>
</div>
<nav aria-label="Main">
  <span class="nav-item active" style="left:313px">Home</span>
  <span class="nav-item" style="left:402px">About Us</span>
  <span class="nav-item" style="left:512px">Products</span>
  <span class="nav-item" style="left:614px">Testimonials</span>
  <span class="nav-item" style="left:756px">Blog</span>
  <span class="nav-item" style="left:833px">Contact Us</span>
</nav>
<div class="icon-btn" style="left:985px;border:2px solid var(--orange);background:#1e1b1a">
  <svg width="22" height="22" viewBox="0 0 24 24" fill="none" stroke="#fff" stroke-width="2"><circle cx="12" cy="8" r="4"/><path d="M4 21c1-4 4-6 8-6s7 2 8 6"/></svg>
</div>
<div class="icon-btn" style="left:1048px;background:var(--orange)">
  <svg width="22" height="22" viewBox="0 0 24 24" fill="#fff"><path d="M6 8h12l1 13H5z"/><path d="M9 8V6a3 3 0 0 1 6 0v2" stroke="#fff" stroke-width="2" fill="none"/></svg>
</div>
<div class="abs hero-dots"><span></span><span></span><span></span></div>
<div class="abs script" style="left:318px;top:150px;font-size:46px;color:var(--white)">Welcome To</div>
<h1 class="abs script" style="left:104px;top:215px;font-size:78px;color:var(--white);white-space:nowrap">Merry Meadow Roasters</h1>
<div class="btn" style="left:353px;top:341px;width:147px;height:57px">Order Now</div>

<!-- PRODUCTS -->
<span class="mark" style="left:585px;top:708px"></span>
<h2 class="title" style="top:740px">Our Products</h2>
<div class="arrow" style="left:53px;top:984px;border:2px solid var(--rust)">
  <svg width="14" height="14" viewBox="0 0 24 24" fill="none" stroke="#3b2a21" stroke-width="3"><path d="M15 5l-7 7 7 7"/></svg>
</div>
<div class="arrow" style="left:1103px;top:978px;width:50px;height:50px;background:var(--rust)">
  <svg width="16" height="16" viewBox="0 0 24 24" fill="none" stroke="#fff" stroke-width="3"><path d="M9 5l7 7-7 7"/></svg>
</div>
<div class="card" style="left:104px">
  <div class="bag" role="img" aria-label="Meadow Gallop coffee bag"></div>
  <div class="card-name">Meadow Gallop</div><div class="btn">Add to cart</div>
</div>
<div class="card featured" style="left:360px">
  <div class="bag" role="img" aria-label="Pony Prance coffee bag"></div>
  <div class="card-name">Pony Prance</div><div class="btn">Add to cart</div>
</div>
<div class="abs badge">12%<small>off</small></div>
<div class="card" style="left:616px">
  <div class="bag" role="img" aria-label="Hurdle Blend coffee bag"></div>
  <div class="card-name">Hurdle Blend</div><div class="btn">Add to cart</div>
</div>
<div class="card" style="left:874px">
  <div class="bag" role="img" aria-label="Trot-n-Roast coffee bag"></div>
  <div class="card-name">Trot-n-Roast</div><div class="btn">Add to cart</div>
</div>

<!-- ABOUT -->
<section class="abs about" role="img" aria-label="Steaming white cup of coffee on a wooden table beside a sack of spilled beans"></section>
<span class="mark light" style="left:104px;top:1442px"></span>
<h2 class="abs script" style="left:103px;top:1490px;font-size:48px;color:var(--white);white-space:nowrap">About Merry Meadow Roasters</h2>
<p class="abs about-text">Lorem ipsum dolor sit amet, consectetur adipiscing elit, sed do mod tempor incididunt ut labore et dolore magna aliqua. Quis ipsum susendisse ultrices gravida. Risus commodo viverra maecenas cuman lacus vel rem ipsum dolor sit amet, consectetur adipiscing elit, sed do eiusmod tempor incididunt ut labore et dolore magna aliqua. Quis ipsum suspendisse ultrices gravida.</p>
<div class="btn" style="left:103px;top:1750px;width:146px;height:55px">Read More</div>

<!-- TESTIMONIALS -->
<section class="abs testi" aria-label="Testimonials"></section>
<span class="mark light" style="left:585px;top:2002px"></span>
<h2 class="title" style="top:2036px;color:var(--white)">Our Customers Testimonials</h2>
<div class="arrow" style="left:51px;top:2213px;border:2px solid var(--white)">
  <svg width="14" height="14" viewBox="0 0 24 24" fill="none" stroke="#fff" stroke-width="3"><path d="M15 5l-7 7 7 7"/></svg>
</div>
<div class="arrow" style="left:1102px;top:2207px;width:50px;height:50px;background:var(--white)">
  <svg width="16" height="16" viewBox="0 0 24 24" fill="none" stroke="#9b3e24" stroke-width="3"><path d="M9 5l7 7-7 7"/></svg>
</div>
<div class="quote" style="left:137px">
  <div class="avatar" role="img" aria-label="Portrait of customer Clara holding a coffee cup"></div>
  <div><div class="stars">★★★★★</div><p>“Lorem ipsum dolor sit amet, nsectetur adipiscing elit, sed do eiusmod empor incididunt ut labore et...</p><div class="who">-Clara</div></div>
</div>
<div class="quote filled" style="left:615px">
  <div class="avatar" role="img" aria-label="Portrait of customer Milo holding a coffee mug"></div>
  <div><div class="stars">★★★★★</div><p>“Lorem ipsum dolor sit amet, nsectetur adipiscing elit, sed do eiusmod empor incididunt ut labore et...</p><div class="who">-Milo</div></div>
</div>

<!-- PORTFOLIO -->
<span class="mark" style="left:585px;top:2495px"></span>
<h2 class="title" style="top:2530px">Our Portfolio</h2>
<div class="shot" style="left:104px;top:2638px;width:393px;height:252px;background:radial-gradient(circle at 50% 50%,#5a483c 0%,#2e2724 45%,#1c1a19 100%)" role="img" aria-label="Latte art in a dark cup"></div>
<div class="shot" style="left:508px;top:2638px;width:289px;height:252px;background:radial-gradient(circle at 70% 15%,#8a7a66,rgba(0,0,0,0) 35%),linear-gradient(160deg,#5a4a3e,#3a2418 60%,#22140d)" role="img" aria-label="Roasted beans spilling from a burlap sack"></div>
<div class="shot" style="left:807px;top:2638px;width:289px;height:252px;background:radial-gradient(circle at 50% 45%,#d8b898,#7a4a2e 55%,#3a2416)" role="img" aria-label="Espresso cup on a wooden board with beans"></div>
<div class="shot" style="left:104px;top:2900px;width:289px;height:254px;background:radial-gradient(ellipse 90px 50px at 40% 68%,#e6ded6,rgba(0,0,0,0) 80%),linear-gradient(180deg,#2a1d17,#5a3a26 85%)" role="img" aria-label="Coffee cup with heart-shaped steam"></div>
<div class="shot" style="left:403px;top:2900px;width:289px;height:254px;background:linear-gradient(160deg,#7a7470,#2a201c 50%,#140e0b)" role="img" aria-label="Hand holding beans beside a grinder"></div>
<div class="shot" style="left:703px;top:2900px;width:393px;height:254px;background:radial-gradient(circle at 50% 45%,#e8d6c0,#a0704c 30%,#4a3a34 70%,#2c2220)" role="img" aria-label="Friends sharing lattes"></div>
<div class="btn" style="left:527px;top:3182px;width:146px;height:54px">View More</div>

<!-- FOOTER -->
<footer class="abs footer" aria-label="Footer"></footer>
<div class="abs brand" style="left:104px;top:3525px;font-size:32px;line-height:36px;width:270px">
  <span class="brand-dot" style="width:20px;height:20px"></span><span>Merry Meadow<br>Roasters</span>
</div>
<div class="foot-head" style="left:446px;top:3436px">Quick Links</div>
<ul class="abs foot-links"><li>HOME</li><li>ABOUT US</li><li>PRODUCTS</li><li>TESTIMONIALS</li><li>BLOG</li><li>CONTACT US</li></ul>
<div class="foot-head" style="left:637px;top:3434px">Contact Us</div>
<div class="contact-row" style="top:3486px">
  <span class="c-icon"><svg width="18" height="18" viewBox="0 0 24 24" fill="#fff"><path d="M6.6 10.8a15 15 0 0 0 6.6 6.6l2.2-2.2a1 1 0 0 1 1-.25 11 11 0 0 0 3.6.6 1 1 0 0 1 1 1V20a1 1 0 0 1-1 1A17 17 0 0 1 3 4a1 1 0 0 1 1-1h3.5a1 1 0 0 1 1 1 11 11 0 0 0 .6 3.6 1 1 0 0 1-.25 1z"/></svg></span>
  <div><b>PHONE NO :</b><br>+1 (555) 010 2040</div>
</div>
<div class="contact-row" style="top:3545px">
  <span class="c-icon"><svg width="16" height="18" viewBox="0 0 24 24" fill="#fff"><path d="M12 2a7 7 0 0 0-7 7c0 5 7 13 7 13s7-8 7-13a7 7 0 0 0-7-7zm0 9.5A2.5 2.5 0 1 1 12 6.5a2.5 2.5 0 0 1 0 5z"/></svg></span>
  <div><b>LOCATION :</b><br>Lorem ipsum dolor<br>amet, consectetur,USA</div>
</div>
<div class="contact-row" style="top:3624px">
  <span class="c-icon"><svg width="18" height="16" viewBox="0 0 24 24" fill="none" stroke="#fff" stroke-width="2"><rect x="3" y="5" width="18" height="14" rx="2"/><path d="M3 7l9 6 9-6"/></svg></span>
  <div><b>EMAIL ADRESS :</b><br>hello@merrymeadowroasters.com</div>
</div>
<div class="foot-head" style="left:916px;top:3434px">Follow Us</div>
<span class="social on" style="left:917px" aria-label="Social profile"></span>
<span class="social" style="left:979px" aria-label="Social profile"></span>
<span class="social" style="left:1040px" aria-label="Social profile"></span>
<div class="abs divider"></div>
<div class="abs copy">Copyright © 2025 Merry Meadow Roasters | All Rights Reserved</div>
<div class="abs beans" role="img" aria-label="Scattered roasted coffee beans"></div>

</body>
</html>
```